Stationery Design Project

We need a stationery design for our Norwegian trucking company. We have existed for about 15 years and our 12 drivers uses relatively new vehicles to transport goods around in northern Norway. Long distance routes with fresh fish og food transport is our main operations.

We have already made alogo that's printed on our trucks. The logo and a picture of our trucks is attached. I think the logo i crappy, but since its already in use, changing it is not an option in this round. Still using a better colour scheme in the overall stationery and more interesting fonts is possible (altso in the logo).

Company details:
Name: Kjelvraket AS
Organisation nr 873 615 309
Post adress: 8642 Raudvik

I like minimalism and simplicity. I am avalibly for questions in normal GMT working hours either here or on mail: ivar@fjordlast.no

Reason: Hi. Im extending the deadline because I needed some time to find a vector file of our logo. Sorry for the inconvenience

Hi, and thanks for all your interest in the project. Some updates:

-          I have decided to commit to using one of the designs. Some designer will get the payment.

-          I have extended the deadline with 24 hours since I needed some time to find our firms vector logo (a slow Swedish man was holding me up)

-          We will not choose a design before the deadline. No need to rush.

-          We have received a lot of great design and think there is a need to specified the product we want to make:

o   Business Card for all our employers. I just need the design and will duplicate with the correct numbers and name myself. The information on should be: Logo, employer’s name, Phone number, email, website, Postal number and address. Use this as a template: logo, Leif Brattvoll, 47382066, Leif@fjordlast.no,, fjordlast.no, 8642 Raudvik. The order and placement of the information is your creative decision.

o   Stickers to put on the goods we travel. On the sticker the should be the following information: Logo, phone number, Tekst and link: Fraktæ av Kjelvraket. Ke du syns? Fjordlast.no/tilbakemelding (this means: Handled by Kjelvraket. What do you think Fjordlast.no/feedback -à the link will be a feedback form). The placement the information and size is your creative decision with some stings: we have been thinking of using Drukko for printing and see that a size about 6x6 cm, 8x5 or something like that. (with 3000 copies our budget is 200 punds). Any suggestions of other suppliers are welcome. Drukko price calculator http://www.drukkolabelhouse.co.uk/digital-litho-printing/printing-labels-tags/stickers/

o   Letterhead with logo, address, phone number and organizational number.

o   Envelopes with logo,address, phone number and organizational number.

Have a nice day.

 

 

• Using the blue colour in the logo and using a similar graphic approch.

```html
<!DOCTYPE html>
<html lang="no">
<head>
<meta charset="utf-8">
<title>Kjelvraket AS – Stationery</title>
<link href="https://fonts.googleapis.com/css2?family=Arimo:wght@400;700&display=swap" rel="stylesheet">
<style>
  :root {
    --navy: #203c8c;
    --navy-deep: #182d6e;
    --sky: #2e7fd0;
    --paper: #ffffff;
    --paper-shade: #e9eaed;
    --silver-light: #f2f3f5;
    --silver-dark: #a9acb3;
    --ink: #3c3c3c;
    --ink-soft: #6b6b6b;
    --stage: #1f1f21;
  }
  * { box-sizing: border-box; margin: 0; padding: 0; }
  html, body { width: 1200px; height: 900px; overflow: hidden; }
  body {
    background: var(--stage);
    font-family: "Arimo", Arial, sans-serif;
    position: relative;
  }
  .piece {
    position: absolute;
    background: linear-gradient(135deg, var(--paper) 0%, var(--paper) 45%, var(--paper-shade) 100%);
    overflow: hidden;
  }
  .piece .swoosh { position: absolute; inset: 0; width: 100%; height: 100%; }
  .brand {
    position: absolute;
    display: flex;
    align-items: center;
    gap: 6px;
    color: var(--navy);
    font-weight: 700;
    line-height: 1;
  }
  .brand-dot { border-radius: 50%; background: var(--sky); flex: none; }
  .web { position: absolute; color: var(--ink-soft); font-weight: 700; }
  .details { position: absolute; color: var(--ink-soft); line-height: 1.25; }
  .details .company { color: var(--ink); font-weight: 700; }

  /* Letterhead */
  .letterhead { left: 48px; top: 50px; width: 352px; height: 500px; }
  .letterhead .brand { left: 26px; top: 26px; font-size: 22px; }
  .letterhead .brand-dot { width: 10px; height: 10px; }
  .letterhead .web { left: 58px; top: 50px; font-size: 9px; }
  .letterhead .side-bar { position: absolute; left: 0; top: 397px; width: 5px; height: 103px; background: var(--navy); }
  .letterhead .details { left: 19px; top: 449px; font-size: 7px; }
  .letterhead .details .company { font-size: 9px; margin-bottom: 2px; }

  /* Business card back */
  .card-back {
    left: 455px; top: 140px; width: 232px; height: 150px; border-radius: 8px;
    background: linear-gradient(150deg, var(--silver-light) 0%, #d3d5da 50%, var(--silver-dark) 100%);
  }
  .card-back .brand { left: 40px; top: 58px; font-size: 21px; }
  .card-back .brand-dot { width: 10px; height: 10px; }
  .card-back .web { left: 56px; top: 90px; font-size: 12px; color: #4a4a4a; }

  /* Business card front */
  .card-front { left: 422px; top: 305px; width: 252px; height: 150px; border-radius: 8px; }
  .card-front .brand { left: 36px; top: 26px; font-size: 15px; }
  .card-front .brand-dot { width: 8px; height: 8px; }
  .card-front .web { left: 40px; top: 46px; font-size: 8px; }
  .card-front .person { position: absolute; left: 30px; top: 108px; font-size: 8px; color: var(--ink-soft); line-height: 1.2; }
  .card-front .person .name { color: var(--navy); font-weight: 700; }
  .card-front .details { left: 118px; top: 104px; font-size: 7px; }
  .card-front .details .company { color: var(--navy); font-size: 8px; }

  /* Envelope back */
  .envelope-back { left: 738px; top: 77px; width: 422px; height: 199px; }
  .envelope-back .brand { left: 148px; top: 22px; font-size: 17px; color: var(--paper); }
  .envelope-back .brand-dot { width: 8px; height: 8px; background: #8cc4f2; }
  .envelope-back .web { left: 170px; top: 42px; font-size: 8px; color: var(--paper); }

  /* Envelope front */
  .envelope-front { left: 738px; top: 294px; width: 422px; height: 200px; }
  .envelope-front .side-bar { position: absolute; left: 0; top: 0; width: 5px; height: 148px; background: var(--navy); }
  .envelope-front .brand { left: 24px; top: 26px; font-size: 17px; }
  .envelope-front .brand-dot { width: 8px; height: 8px; }
  .envelope-front .details { left: 27px; top: 158px; font-size: 6px; }
  .envelope-front .details .company { font-size: 7px; margin-bottom: 1px; }

  /* Sticker */
  .sticker { left: 838px; top: 566px; width: 224px; height: 224px; border-radius: 50%; }
  .sticker .brand { left: 30px; top: 56px; font-size: 19px; }
  .sticker .brand-dot { width: 10px; height: 10px; }
  .sticker .web { left: 40px; top: 82px; font-size: 15px; }
  .sticker .details { left: 30px; top: 124px; font-size: 10.5px; }
  .sticker .details .company { color: var(--navy); font-size: 12px; margin-bottom: 1px; }
</style>
</head>
<body>

<section class="piece letterhead" aria-label="Letterhead">
  <svg class="swoosh" viewBox="0 0 352 500" preserveAspectRatio="none" aria-hidden="true">
    <defs>
      <linearGradient id="lh-silver" x1="0" x2="1"><stop offset="0" stop-color="#eceef1"/><stop offset="1" stop-color="#a7abb2"/></linearGradient>
    </defs>
    <path d="M300 0 C360 120 360 330 280 500 L352 500 L352 0 Z" fill="url(#lh-silver)"/>
    <path d="M288 0 C352 130 350 360 238 500 L262 500 C360 360 366 130 302 0 Z" fill="var(--navy)"/>
    <path d="M296 60 C350 170 345 380 290 500 L320 500 C365 370 360 170 296 60 Z" fill="var(--navy)"/>
    <path d="M330 180 C352 280 348 420 330 500 L352 500 L352 180 Z" fill="var(--navy-deep)"/>
  </svg>
  <div class="brand"><span class="brand-dot"></span>Kjelvraket</div>
  <div class="web">fjordlast.no</div>
  <div class="side-bar"></div>
  <div class="details">
    <div class="company">Kjelvraket AS</div>
    <div>Organisation nr 873 615 309</div>
    <div>Post adress: 8642 Raudvik</div>
  </div>
</section>

<section class="piece card-back" aria-label="Business card, back">
  <svg class="swoosh" viewBox="0 0 232 150" preserveAspectRatio="none" aria-hidden="true">
    <rect x="0" y="0" width="5" height="150" fill="var(--navy)"/>
    <path d="M200 0 C228 50 224 110 196 150 L206 150 C232 110 234 50 210 0 Z" fill="var(--navy)"/>
    <path d="M214 20 C234 70 230 120 214 150 L222 150 C238 115 238 70 220 20 Z" fill="var(--navy)"/>
  </svg>
  <div class="brand"><span class="brand-dot"></span>Kjelvraket</div>
  <div class="web">fjordlast.no</div>
</section>

<section class="piece card-front" aria-label="Business card, front">
  <svg class="swoosh" viewBox="0 0 252 150" preserveAspectRatio="none" aria-hidden="true">
    <defs>
      <linearGradient id="cf-silver" x1="0" x2="1"><stop offset="0" stop-color="#e5e7ea"/><stop offset="1" stop-color="#b3b6bc"/></linearGradient>
    </defs>
    <rect x="0" y="90" width="8" height="60" fill="url(#cf-silver)"/>
    <path d="M226 0 C256 50 250 110 212 150 L224 150 C258 110 262 50 236 0 Z" fill="var(--navy)"/>
    <path d="M238 30 C256 75 252 120 236 150 L252 150 L252 30 Z" fill="var(--navy)"/>
  </svg>
  <div class="brand"><span class="brand-dot"></span>Kjelvraket</div>
  <div class="web">fjordlast.no</div>
  <div class="person">
    <div class="name">Leif Brattvoll</div>
    <div>47382066</div>
  </div>
  <div class="details">
    <div class="company">Kjelvraket AS</div>
    <div>Organisation nr 873 615 309</div>
    <div>Post adress: 8642 Raudvik</div>
    <div>Leif@fjordlast.no</div>
  </div>
</section>

<section class="piece envelope-back" aria-label="Envelope, back">
  <svg class="swoosh" viewBox="0 0 422 199" preserveAspectRatio="none" aria-hidden="true">
    <path d="M0 0 L422 0 L422 8 C405 40 330 45 270 52 C240 56 222 72 211 72 C200 72 182 56 152 52 C92 45 17 40 0 8 Z" fill="var(--navy)"/>
  </svg>
  <div class="brand"><span class="brand-dot"></span>Kjelvraket</div>
  <div class="web">fjordlast.no</div>
</section>

<section class="piece envelope-front" aria-label="Envelope, front">
  <svg class="swoosh" viewBox="0 0 422 200" preserveAspectRatio="none" aria-hidden="true">
    <defs>
      <linearGradient id="ef-silver" x1="0" x2="1"><stop offset="0" stop-color="#e8eaed"/><stop offset="1" stop-color="#a9adb4"/></linearGradient>
    </defs>
    <rect x="0" y="148" width="5" height="52" fill="url(#ef-silver)"/>
    <path d="M400 0 C422 60 420 140 410 200 L422 200 L422 0 Z" fill="url(#ef-silver)"/>
    <path d="M382 0 C418 60 414 140 378 200 L390 200 C426 140 428 60 394 0 Z" fill="var(--navy)"/>
    <path d="M390 30 C420 85 416 150 398 200 L410 200 C428 150 430 85 398 30 Z" fill="var(--navy)"/>
  </svg>
  <div class="side-bar"></div>
  <div class="brand"><span class="brand-dot"></span>Kjelvraket</div>
  <div class="details">
    <div class="company">Kjelvraket AS</div>
    <div>Organisation nr 873 615 309</div>
    <div>Post adress: 8642 Raudvik</div>
    <div>Leif@fjordlast.no</div>
  </div>
</section>

<section class="piece sticker" aria-label="Sticker">
  <svg class="swoosh" viewBox="0 0 224 224" preserveAspectRatio="none" aria-hidden="true">
    <path d="M178 18 C222 70 220 160 170 210 L182 206 C230 160 232 70 190 26 Z" fill="var(--navy)"/>
    <path d="M196 40 C226 90 222 160 190 200 L224 224 L224 40 Z" fill="var(--navy)"/>
  </svg>
  <div class="brand"><span class="brand-dot"></span>Kjelvraket</div>
  <div class="web">fjordlast.no</div>
  <div class="details">
    <div class="company">Kjelvraket AS</div>
    <div>Organisation nr 873 615 309</div>
    <div>Post adress: 8642 Raudvik</div>
    <div>Leif@fjordlast.no</div>
  </div>
</section>

</body>
</html>
```